Coastline Premier Retreats Business Card Design

Design a business card for Coastline Premier Retreats. Look at the website for colors and reference. Card should have logo, name, title, office number, mobile number, email, URL and a tagline like, "Luxury Hotel & Resort Email Marketing" (This might change).

https://www.coastlinepremierretreats.example

The rest I will leave up to your imagination.

Contact Information for Business Card

Logo, name, title, office number, mobile number, email, URL and a tagline like, "Luxury Hotel & Resort Email Marketing" (This might change).

```html
<!DOCTYPE html>
<html lang="en">
<head>
<meta charset="utf-8">
<title>Coastline Premier Retreats – Business Card</title>
<link href="https://fonts.googleapis.com/css2?family=Montserrat:wght@400;600;700;800&display=swap" rel="stylesheet">
<style>
  :root {
    --stage: #2b2b2d;
    --card: #262628;
    --card-deep: #1f1f21;
    --orange: #f47920;
    --white: #ffffff;
    --text: #e9e9ea;
  }
  * { box-sizing: border-box; margin: 0; padding: 0; }
  html, body { width: 1200px; height: 900px; overflow: hidden; }
  body {
    background: var(--stage);
    font-family: "Montserrat", sans-serif;
    position: relative;
  }
  .card {
    position: absolute;
    width: 560px;
    height: 320px;
    background: var(--card);
    border-radius: 16px;
    border-bottom: 5px solid var(--orange);
    overflow: hidden;
    box-shadow: 0 18px 40px rgba(0,0,0,.45);
  }
  .card--back { left: 30px; top: 290px; }
  .card--front { left: 610px; top: 290px; }

  /* back side */
  .back-pattern {
    position: absolute; inset: 0;
    background: linear-gradient(135deg, #2a2a2c 0%, var(--card-deep) 100%);
  }
  .back-brand {
    position: absolute;
    left: 50%; top: 50%;
    transform: translate(-50%, -50%);
    display: flex; align-items: center; gap: 8px;
    background: var(--card);
    padding: 8px 12px;
  }
  .back-brand__mark { width: 10px; height: 10px; background: var(--orange); }
  .back-brand__name {
    color: var(--orange); font-weight: 700; font-size: 13px;
    letter-spacing: .06em; text-transform: uppercase; white-space: nowrap;
  }

  /* front side */
  .brand {
    position: absolute; left: 34px; top: 112px;
    width: 200px;
    display: flex; align-items: center; gap: 10px;
  }
  .brand__mark { width: 12px; height: 12px; background: var(--orange); flex: none; }
  .brand__name {
    color: var(--white); font-weight: 800; font-size: 19px;
    line-height: 1.1; text-transform: uppercase; letter-spacing: .02em;
  }
  .divider {
    position: absolute; left: 262px; top: 28px;
    width: 2px; height: 160px; background: var(--orange);
  }
  .contact { position: absolute; left: 280px; top: 26px; color: var(--text); }
  .contact__name { color: var(--orange); font-weight: 700; font-size: 19px; }
  .contact__title { font-size: 11px; margin: 1px 0 10px; }
  .contact__address { font-size: 10.5px; line-height: 1.4; margin-bottom: 8px; }
  .contact__list { list-style: none; font-size: 10.5px; }
  .contact__list li { display: flex; align-items: center; gap: 8px; height: 17px; }
  .contact__list svg { width: 11px; height: 11px; fill: var(--orange); flex: none; }
  .bands { position: absolute; left: 0; bottom: 0; width: 560px; height: 130px; }
  .tagline {
    position: absolute; right: 250px; top: 262px;
    color: var(--orange); font-weight: 700; font-size: 11.5px;
    white-space: nowrap;
  }
</style>
</head>
<body>

<section class="card card--back" aria-label="Card back">
  <div class="back-pattern" role="img" aria-label="Repeating tone-on-tone brand name pattern"></div>
  <div class="back-brand">
    <span class="back-brand__mark"></span>
    <span class="back-brand__name">Coastline Premier Retreats</span>
  </div>
</section>

<section class="card card--front" aria-label="Card front">
  <div class="brand">
    <span class="brand__mark"></span>
    <span class="brand__name">Coastline Premier Retreats</span>
  </div>

  <div class="divider"></div>

  <div class="contact">
    <h1 class="contact__name">Daniel Rourke</h1>
    <p class="contact__title">Owner</p>
    <p class="contact__address">145 Harbor Ave. Suite 210<br>Portland, OR 97201</p>
    <ul class="contact__list">
      <li><svg viewBox="0 0 24 24"><path d="M6.6 10.8a15.1 15.1 0 0 0 6.6 6.6l2.2-2.2c.3-.3.7-.4 1-.2 1.1.4 2.3.6 3.6.6.6 0 1 .4 1 1V20c0 .6-.4 1-1 1A17 17 0 0 1 3 4c0-.6.4-1 1-1h3.5c.6 0 1 .4 1 1 0 1.3.2 2.5.6 3.6.1.3 0 .7-.2 1z"/></svg>555.014.2210 x 204</li>
      <li><svg viewBox="0 0 24 24"><path d="M7 1h10a2 2 0 0 1 2 2v18a2 2 0 0 1-2 2H7a2 2 0 0 1-2-2V3a2 2 0 0 1 2-2zm0 3v14h10V4zm5 15.5a1 1 0 1 0 0 2 1 1 0 0 0 0-2z"/></svg>555.019.4836</li>
      <li><svg viewBox="0 0 24 24"><path d="M2 5h20v14H2zm2 2v.5l8 5 8-5V7z"/></svg>info@coastlinepremierretreats.example</li>
      <li><svg viewBox="0 0 24 24"><path d="M12 2a10 10 0 1 0 0 20 10 10 0 0 0 0-20zm-1 17.9A8 8 0 0 1 4.1 11H8c.1 3.3 1.1 6.3 3 8.9zM8 9H4.1A8 8 0 0 1 11 4.1C9.1 6.7 8.1 6 8 9zm5 10.9c1.9-2.6 2.9-5.6 3-8.9h3.9a8 8 0 0 1-6.9 8.9zM16 9c-.1-3-1.1-2.3-3-4.9A8 8 0 0 1 19.9 9z"/></svg>www.coastlinepremierretreats.example</li>
    </ul>
  </div>

  <svg class="bands" viewBox="0 0 560 130" aria-hidden="true">
    <polygon points="0,92 320,92 310,120 0,120" fill="var(--orange)"/>
    <polygon points="336,40 560,40 560,84 322,84" fill="var(--white)"/>
  </svg>

  <p class="tagline">Luxury Hotel &amp; Resort Email Marketing</p>
</section>

</body>
</html>
```